Web Design Project

Please take a look at my current aged website www.talvikhrconsulting.com and my newly designed logo and business cards. I would like a new fresh updated look to my website and my new designs incorporated.
Updates

  Good Morning Everyone

Due to an Austrralian licencing issue I have had to have my logo slightly redesigned.

Would you please be able to look at the newly uploaded files and revise your designs.

Thanks so much.  I am very happy with the calibre and quality of the designs so far.

kind Regards

Marla

Industry/Entity Type

Business

Requirements
Must have
• the exisiting pages and fresh new graphics and a real commitment to my palette of lime green, turqouise and black.

```html
<!DOCTYPE html>
<html lang="en">
<head>
<meta charset="utf-8">
<title>Talvik HR Consulting</title>
<link href="https://fonts.googleapis.com/css2?family=Source+Sans+3:ital,wght@0,300;0,400;0,600;0,700;1,400&display=swap" rel="stylesheet">
<style>
:root{
  --cyan:#1ab3d6;
  --green:#7ab32e;
  --ink:#333;
  --muted:#555;
  --soft:#777;
  --rule:#dcdcdc;
  --footer:#efefef;
}
*{margin:0;padding:0;box-sizing:border-box}
html,body{width:879px;height:1200px;overflow:hidden;background:#fff}
body{font-family:"Source Sans 3",Arial,sans-serif;color:var(--ink);position:relative}
.abs{position:absolute}
a{color:inherit;text-decoration:none}

.topbar{left:0;top:0;width:879px;height:28px;background:var(--cyan)}
.toplinks{right:86px;top:8px;font-size:10px;color:#fff}
.toplinks span{margin:0 7px;opacity:.8}

.header{left:0;top:28px;width:879px;height:142px;background:linear-gradient(#fff,#f6f6f6)}
.brand-mark{left:30px;top:57px;width:92px;height:92px;border-radius:50%;border:4px solid var(--cyan)}
.brand-name{left:137px;top:62px;color:var(--cyan);font-weight:600;line-height:1}
.brand-name .big{font-size:47px;display:block;letter-spacing:-1px}
.brand-name .small{font-size:25px;display:block;margin-top:2px}
.search{left:645px;top:61px;width:196px;height:23px;border:1px solid #ddd;border-radius:6px;background:#fafafa;font-size:9.5px;color:#999;padding:5px 8px}
.search svg{position:absolute;right:8px;top:4px}

.nav{top:130px;left:333px;display:flex;align-items:center;font-size:12px;font-weight:600;color:var(--green)}
.nav .home{background:var(--green);color:#fff;width:72px;height:23px;border-radius:3px;display:flex;align-items:center;justify-content:center}
.nav .sep{color:var(--green);margin:0 22px;font-weight:400}
.nav .first{margin-left:29px}

.hero{left:0;top:170px;width:879px;height:312px;background:linear-gradient(90deg,#f7f7f7 0%,#fff 55%,#f2f2f2 100%)}
.hero-title{left:61px;top:236px;font-size:25px;font-weight:400;color:var(--ink)}
.hero-title em{font-style:normal;color:var(--green)}
.hero-text{left:62px;top:273px;width:395px;font-size:10.5px;line-height:14.6px;color:var(--soft);font-weight:300}
.btn{left:60px;top:359px;width:101px;height:25px;background:var(--green);border-radius:3px;color:#fff;font-size:11px;display:flex;align-items:center;justify-content:center;gap:6px}
.dots{left:61px;top:417px;display:flex;gap:4px}
.dots i{width:11px;height:11px;border-radius:50%;background:var(--green);display:block}
.hero-art{left:515px;top:195px;width:290px;height:287px;background:radial-gradient(circle at 40% 35%,#3cc4e2 0%,#1aa7c9 35%,#e6eef0 70%,rgba(255,255,255,0) 100%)}

.side{left:25px;top:500px;width:221px}
.h2{font-size:15.5px;font-weight:400;color:var(--ink)}
.news-date{font-size:10px;color:var(--green);font-weight:600;margin-top:14px}
.news-text{font-size:9.5px;line-height:13.7px;color:var(--muted);margin-top:3px}
.news-more{font-size:9.5px;color:var(--green);margin-top:6px}
.news-more b{font-weight:600}
.dash{border-top:1px dashed #ccc;margin:15px 0 0}
.testimonial{margin-top:9px;background:#f5f5f5;padding:10px 15px 12px;margin-left:-1px}
.testimonial p{font-style:italic;font-size:9.5px;line-height:14.6px;color:var(--green)}
.testimonial .by{font-size:9.5px;color:var(--green);margin-top:11px}

.main{left:271px;top:500px;width:582px}
.main .rule{border-top:1px solid var(--rule);margin-top:6px}
.main p{font-size:9.5px;line-height:15.4px;color:var(--muted);margin-top:9px}
.services-title{left:270px;top:706px;font-size:13.5px}
.services-rule{left:271px;top:728px;width:560px;border-top:1px solid var(--rule)}
.card{top:748px;width:181px}
.card .photo{height:75px;border:1px solid #ccc;background:linear-gradient(135deg,#d8dde2,#8a97a5 60%,#3b4654)}
.card h3{font-size:10.5px;font-weight:400;margin-top:19px;color:var(--ink)}
.card p{font-size:9.5px;line-height:15.4px;color:var(--muted);margin-top:7px}
.card .more{font-size:10px;font-weight:600;margin-top:10px;color:var(--ink)}

.footer{left:0;top:970px;width:879px;height:185px;background:var(--footer);border-top:2px solid #e4e4e4}
.fh{font-size:14.5px;color:#555}
.links{left:38px;top:998px}
.linkcols{display:flex;gap:44px;margin-top:13px;font-size:9.5px;color:var(--soft)}
.linkcols li{list-style:none;line-height:19.6px}
.linkcols li::before{content:"▸";font-size:6px;margin-right:7px;color:#999;vertical-align:2px}
.about{left:277px;top:998px;width:290px}
.about p{font-size:9.5px;line-height:17px;color:var(--soft);margin-top:13px;padding-left:2px}
.flogo{left:435px;top:1098px;display:flex;align-items:center;gap:6px;color:#888;font-weight:600}
.flogo i{width:40px;height:40px;border-radius:50%;border:2px solid #999;display:block}
.flogo span{font-size:17px;line-height:1}
.flogo small{display:block;font-size:10px;font-weight:600}
.follow{left:633px;top:998px}
.icons{display:flex;gap:4px;margin-top:10px}
.icons i{width:23px;height:23px;border-radius:50%;background:#fff;border:1px solid #ddd;display:block}
.connect{font-size:9.5px;color:var(--soft);line-height:19.6px;margin-top:6px}
.connect b{font-weight:400;color:var(--ink)}

.bottombar{left:0;top:1155px;width:879px;height:45px;background:var(--cyan);color:#fff;font-size:9.5px;padding:18px 27px}
</style>
</head>
<body>

<div class="abs topbar"></div>
<div class="abs toplinks">Register<span>|</span>Log In<span>|</span>Faq</div>

<div class="abs header"></div>
<div class="abs brand-mark"></div>
<div class="abs brand-name"><span class="big">Talvik</span><span class="small">HR Consulting</span></div>
<div class="abs search">type your word
  <svg width="16" height="14" viewBox="0 0 16 14"><circle cx="6" cy="6" r="4.5" fill="none" stroke="#aaa" stroke-width="1.6"/><line x1="9.5" y1="9.5" x2="14" y2="13" stroke="#aaa" stroke-width="2"/></svg>
</div>
<nav class="abs nav">
  <a class="home">Home</a>
  <a class="first">Our Services</a><span class="sep">|</span>
  <a>Our Consultants</a><span class="sep">|</span>
  <a>Our Fees</a><span class="sep">|</span>
  <a>Contact Us</a>
</nav>

<section class="abs hero"></section>
<h1 class="abs hero-title"><em>Talvik HR Consulting</em> Punch Line</h1>
<p class="abs hero-text">We like solving questions that arises in such projects as these helps us to grow also. When considering advanced web development project, finding the right answers to the hard questions is a challenge for any firm, it includes expertise and enables. Brightwave Solutions to specialize in advanced projects and ongoing projects that require permanent support and maintenance.</p>
<a class="abs btn">VIEW MORE <svg width="7" height="8" viewBox="0 0 7 8"><path d="M0 0L7 4L0 8Z" fill="#fff"/></svg></a>
<div class="abs dots"><i></i><i></i><i></i><i></i><i></i></div>
<div class="abs hero-art" role="img" aria-label="Figures in turquoise lifting a globe, with a faded pair in the background"></div>

<aside class="abs side">
  <h2 class="h2">Latest News &amp; Blog</h2>
  <div class="news-date">20.March.2012</div>
  <p class="news-text">Brightwave Solutions provides you the Search Engine Optimization making your website search engine friendly. So that the website can achieve top position and ranking in the Internet searches.</p>
  <div class="news-more"><b>READ MORE</b> &nbsp;|&nbsp; 2 days ago</div>
  <div class="dash"></div>
  <div class="news-date">20.March.2012</div>
  <p class="news-text">Brightwave Solutions provides you the Search Engine Optimization making your website search engine friendly.</p>
  <div class="news-more"><b>READ MORE</b> &nbsp;|&nbsp; 2 days ago</div>
  <div class="dash"></div>
  <h2 class="h2" style="margin-top:17px">Testimonials</h2>
  <div class="testimonial">
    <p>We like solving questions that arises in such projects as these helps us to grow also. When considering advanced web development project, finding the right answers to the hard questions is a challenge for any firm, it includes expertise</p>
    <div class="by">BY AUTHOR NAME &nbsp;|&nbsp; 2 days ago</div>
  </div>
</aside>

<section class="abs main">
  <h2 class="h2">What can Talvik HR Consulting do for me?</h2>
  <div class="rule"></div>
  <p>Brightwave Solutions is a web service company, offering a wide range of services which range from designing and development, that is covering almost all the fields in the best possible way. To be the best we know what and how to present beautifully the working of the client's need and their advantages be highlighted. We act in accordance with the Industry certified processes to deliver the best to our clients all over the world. Over years we have built a strong reputation in providing website design and web development services.</p>
  <p style="margin-top:15px">Thus, Wanna get ahead in the competition with other websites…. Brightwave Solutions provide you with an attractive and most convincing website to enhance your marketing goals.<br>The only way to success is through the right path and that's what we provide you. None of the other companies has the result we do. So stick to the best that's how you will be the best don't opt for the second best. Our expertise does not limit itself to web development but also it includes Web Hosting</p>
</section>

<h2 class="abs services-title h2">Take a Look at Our Services</h2>
<div class="abs services-rule"></div>

<article class="abs card" style="left:271px">
  <div class="photo" role="img" aria-label="Business colleagues talking in an office"></div>
  <h3>OUR HEADLINE GOES HERE</h3>
  <p>Brightwave Solutions is a web service company, offering a wide range of services which range from designing and development,</p>
  <div class="more">READ MORE</div>
</article>
<article class="abs card" style="left:471px">
  <div class="photo" role="img" aria-label="Team meeting around a conference table"></div>
  <h3>OUR HEADLINE GOES HERE</h3>
  <p>Brightwave Solutions is a web service company, offering a wide range of services which range from designing and development,</p>
  <div class="more">READ MORE</div>
</article>
<article class="abs card" style="left:671px">
  <div class="photo" role="img" aria-label="Group of business professionals standing together"></div>
  <h3>OUR HEADLINE GOES HERE</h3>
  <p>Brightwave Solutions is a web service company, offering a wide range of services which range from designing and development,</p>
  <div class="more">READ MORE</div>
</article>

<footer class="abs footer"></footer>
<div class="abs links">
  <h2 class="fh">Usefull links</h2>
  <div class="linkcols">
    <ul><li>Home</li><li>Our Services</li><li>Our Consultants</li><li>Our Fees</li></ul>
    <ul><li>Support</li><li>Contact Us</li></ul>
  </div>
</div>
<div class="abs about">
  <h2 class="fh">Little About Company</h2>
  <p>Brightwave Solutions is a web service company, offering a wide range of services which range from designing and development, that is covering almost all the fields in the best possible way.<br>To be the best</p>
</div>
<div class="abs flogo"><i></i><div><span>Talvik</span><small>HR Consulting</small></div></div>
<div class="abs follow">
  <h2 class="fh">Follow Us</h2>
  <div class="icons"><i></i><i></i><i></i></div>
  <div class="connect">Connect with <b>Chirpline</b><br>Connect with <b>ProLink</b><br>Connect with <b>Friendhub</b></div>
</div>

<div class="abs bottombar">© 2012 Company Name &nbsp;|&nbsp; All right reserved</div>

</body>
</html>
```